Visitenkarten-Design für das Business mit Gesundheit& Beauty
Zielgruppe
Ich bin selbständige Vertriebspartnerin von Vk. Die Visitenkarten sollen nicht zu verspielt wirken, eher geschäftlich. Dennoch könnte eine Verbindung zu den Bereichen Gesundheit & Beuuty dazukommen .
Hauptproduktmerkmal ist zum Beispiel die Aloe Vera, Naturprodukte.. mehr Infos auf : www.bettina-kolmar-beispiel.de
Instagram :bettikolmar
Eventuell könnte mein Slogan mit 'just more' noch einfließen, muss aber nicht. Bin für Ideen offen...
Aufgabenstellung
elegant und zeitlos, aber weich
Vielleicht eine goldene Aloe Vera irgendwie mit drauf?
Habe bei den dateien mal ein paar Screenshots hinzugefügt was ich recht schön fand

```html
<!DOCTYPE html>
<html lang="de">
<head>
<meta charset="utf-8">
<title>Visitenkarte Bettina Kolmar</title>
<link href="https://fonts.googleapis.com/css2?family=Josefin+Sans:wght@300;400;600&family=Open+Sans:wght@400;600;700&display=swap" rel="stylesheet">
<style>
  :root {
    --backdrop: #2a2b2e;
    --card-white: #ffffff;
    --beige-light: #efe4d2;
    --beige-mid: #ddcbad;
    --beige-deep: #c9b48f;
    --ink: #2b2723;
    --gold: #c59a5c;
    --grey-text: #5a5550;
    --rule: #8c8680;
  }
  * { box-sizing: border-box; margin: 0; padding: 0; }
  html, body { width: 1200px; height: 898px; overflow: hidden; }
  body {
    background: var(--backdrop);
    display: flex;
    align-items: center;
    justify-content: center;
    gap: 48px;
  }
  .card {
    position: relative;
    width: 530px;
    height: 310px;
    border-radius: 22px;
    overflow: hidden;
    box-shadow: 0 14px 34px rgba(0,0,0,.45);
  }

  /* Front */
  .card-front { background: var(--beige-mid); }
  .leaf-pattern {
    position: absolute; inset: 0;
    background:
      radial-gradient(ellipse at 30% 25%, var(--beige-light) 0%, transparent 60%),
      radial-gradient(ellipse at 75% 80%, var(--beige-deep) 0%, transparent 65%),
      linear-gradient(135deg, var(--beige-light), var(--beige-mid) 55%, var(--beige-deep));
  }
  .brand {
    position: absolute; inset: 0;
    display: flex; flex-direction: column;
    align-items: center; justify-content: center;
    gap: 12px;
    font-family: "Josefin Sans", sans-serif;
    color: var(--ink);
  }
  .brand-name {
    font-size: 38px; font-weight: 400; letter-spacing: 3px;
    text-transform: uppercase;
  }
  .brand-tagline {
    font-size: 12px; font-weight: 400; letter-spacing: 3px;
    text-transform: uppercase;
  }

  /* Back */
  .card-back {
    background: var(--card-white);
    display: flex; align-items: center;
    padding: 0 34px;
  }
  .back-brand {
    width: 220px;
    display: flex; flex-direction: column; gap: 8px;
    font-family: "Josefin Sans", sans-serif; color: var(--ink);
  }
  .back-brand .brand-name { font-size: 24px; letter-spacing: 2px; }
  .back-brand .brand-tagline { font-size: 8px; letter-spacing: 2.2px; }
  .divider { width: 1px; height: 120px; background: var(--rule); margin: 0 26px 0 14px; }
  .contact { font-family: "Open Sans", sans-serif; color: var(--grey-text); }
  .contact-name {
    font-size: 15px; font-weight: 700; color: var(--gold);
    text-transform: uppercase; letter-spacing: .5px;
  }
  .contact-role { font-size: 10px; margin-bottom: 14px; }
  .contact-list { list-style: none; display: flex; flex-direction: column; gap: 6px; }
  .contact-list li { display: flex; align-items: center; gap: 8px; font-size: 12px; }
  .contact-list svg { width: 11px; height: 11px; fill: var(--gold); flex: none; }
</style>
</head>
<body>

  <section class="card card-front">
    <div class="leaf-pattern" role="img" aria-label="Soft gold and beige leaf pattern background"></div>
    <div class="brand">
      <div class="brand-name">Bettina Kolmar</div>
      <div class="brand-tagline">Health, Beauty &amp; More</div>
    </div>
  </section>

  <section class="card card-back">
    <div class="back-brand">
      <div class="brand-name">Bettina Kolmar</div>
      <div class="brand-tagline">Health, Beauty &amp; More</div>
    </div>
    <div class="divider"></div>
    <div class="contact">
      <div class="contact-name">Jonas Feldberg</div>
      <div class="contact-role">Australasian</div>
      <ul class="contact-list">
        <li>
          <svg viewBox="0 0 24 24" aria-hidden="true"><path d="M6.6 10.8a15 15 0 0 0 6.6 6.6l2.2-2.2a1 1 0 0 1 1-.25 11.4 11.4 0 0 0 3.6.57 1 1 0 0 1 1 1V20a1 1 0 0 1-1 1A17 17 0 0 1 3 4a1 1 0 0 1 1-1h3.5a1 1 0 0 1 1 1c0 1.25.2 2.45.57 3.57a1 1 0 0 1-.25 1z"/></svg>
          0171 552 0394
        </li>
        <li>
          <svg viewBox="0 0 24 24" aria-hidden="true"><path d="M2 5h20v14H2z M2 5l10 8 10-8" fill="none" stroke="#c59a5c" stroke-width="2.4"/></svg>
          info@kolmar-mail.de
        </li>
        <li>
          <svg viewBox="0 0 24 24" aria-hidden="true"><circle cx="12" cy="12" r="9.5" fill="none" stroke="#c59a5c" stroke-width="2.4"/><path d="M2.5 12h19M12 2.5c3 3 3 16 0 19M12 2.5c-3 3-3 16 0 19" fill="none" stroke="#c59a5c" stroke-width="1.8"/></svg>
          www.bettina-kolmar-beispiel.de
        </li>
        <li>
          <svg viewBox="0 0 24 24" aria-hidden="true"><path d="M12 2a7 7 0 0 0-7 7c0 5.2 7 13 7 13s7-7.8 7-13a7 7 0 0 0-7-7zm0 9.5A2.5 2.5 0 1 1 12 6.5a2.5 2.5 0 0 1 0 5z"/></svg>
          Lindenweg 14, 50667 Köln
        </li>
      </ul>
    </div>
  </section>

</body>
</html>
```